Real Estate Brokerage Stationery Designs

I am looking to have presentation folders with business card slots on both sides along with pockets on both sides. I've attached logos, website colors along with current business card designs.

I am looking for envelope designs both big and small. Possibly new business card designs, notepad templates for big and small notepads. Letterhead designs. Pop socket designs. Realtors name badge designs.

www.brightholdrealty.example

```html
<!DOCTYPE html>
<html lang="en">
<head>
<meta charset="utf-8">
<title>Brighthold Realty Stationery</title>
<link rel="stylesheet" href="https://fonts.googleapis.com/css2?family=Open+Sans:wght@400;600&family=Tinos&display=swap">
<style>
  :root {
    --backdrop: #a9a8a9;
    --paper: #f1f1f1;
    --paper-edge: #e2e2e2;
    --brand-blue: #0057a8;
    --ink: #4a4a4a;
    --ink-soft: #5c5c5c;
    --white: #ffffff;
  }
  * { margin: 0; padding: 0; box-sizing: border-box; }
  html, body { width: 1200px; height: 871px; overflow: hidden; }
  body { background: var(--backdrop); position: relative; font-family: "Open Sans", Arial, sans-serif; }

  .sheet { position: absolute; background: linear-gradient(90deg, var(--paper) 0%, var(--paper-edge) 100%); }

  .envelope-front { left: 54px; top: 216px; width: 560px; height: 254px; }
  .envelope-back { left: 54px; top: 501px; width: 560px; height: 254px; overflow: hidden; }
  .letterhead { left: 638px; top: 57px; width: 522px; height: 734px; }

  .brand-name { font-family: "Open Sans", Arial, sans-serif; font-weight: 600; color: var(--brand-blue); line-height: 1.15; text-align: center; }
  .brand-mark { display: inline-block; width: 10px; height: 10px; background: var(--brand-blue); vertical-align: middle; margin-right: 6px; }

  .envelope-front .return-block { position: absolute; left: 28px; top: 46px; width: 140px; text-align: center; }
  .envelope-front .brand-name { font-size: 17px; }
  .return-address { margin-top: 10px; font-size: 7px; color: var(--ink); line-height: 1.4; }

  .flap { position: absolute; left: 0; top: 0; width: 560px; height: 94px; }
  .flap-brand { position: absolute; left: 0; top: 28px; width: 560px; font-size: 17px; color: var(--white); }
  .flap-brand .brand-mark { background: var(--white); }

  .letterhead .brand-name { position: absolute; left: 0; top: 100px; width: 522px; font-size: 19px; }
  .letter { position: absolute; left: 48px; top: 180px; width: 431px; font-family: "Tinos", "Times New Roman", serif; color: var(--ink-soft); }
  .letter-date { font-size: 9px; }
  .recipient { margin-top: 28px; font-size: 9px; line-height: 12px; }
  .letter-body p { font-size: 7.6px; line-height: 12px; text-align: justify; margin-top: 12px; }
  .letter-body p:first-child { margin-top: 22px; }
  .signature { margin-top: 40px; width: 110px; height: 44px; background: linear-gradient(90deg, #e6e6e6, #dcdcdc); border-radius: 3px; }

  .contact-list { position: absolute; left: 62px; top: 669px; list-style: none; font-size: 7px; color: var(--ink); }
  .contact-list li { height: 10.4px; display: flex; align-items: center; gap: 6px; }
  .contact-list svg { width: 8px; height: 8px; fill: var(--brand-blue); }
  .office-address { position: absolute; right: 53px; top: 681px; font-size: 7px; color: var(--ink); text-align: right; line-height: 1.45; }
</style>
</head>
<body>

<section class="sheet envelope-front" aria-label="Envelope front">
  <div class="return-block">
    <div class="brand-name"><span class="brand-mark"></span>Brighthold Realty</div>
    <p class="return-address">2400 Harbor Point Rd, Suite 310,<br>Lakeview, FL 33400</p>
  </div>
</section>

<section class="sheet envelope-back" aria-label="Envelope back">
  <svg class="flap" viewBox="0 0 560 94" aria-hidden="true">
    <path d="M0 0 H560 L548 60 Q542 94 510 94 H50 Q18 94 12 60 Z" fill="var(--brand-blue)"/>
  </svg>
  <div class="brand-name flap-brand"><span class="brand-mark"></span>Brighthold Realty</div>
</section>

<section class="sheet letterhead" aria-label="Letterhead">
  <div class="brand-name"><span class="brand-mark"></span>Brighthold Realty</div>

  <article class="letter">
    <p class="letter-date">Cartagena de Indias, Ocober 12,2015</p>
    <p class="recipient">Sr.<br>MATEO RUIZ<br>Web Master<br>City</p>
    <div class="letter-body">
      <p>Contrary to popular belief, Lorem Ipsum is not simply random text. It has roots in a piece of classical Latin literature from 45 BC, making it over 2000 years old. Richard Mallory, a Latin professor at Westbrook College in Virginia, looked up one of the more obscure Latin words, consectetur, from a Lorem Ipsum passage, and going through the cites of the word in classical literature,</p>
      <p>discovered the undoubtable source. Lorem Ipsum comes from sections 1.10.32 and 1.10.33 of "de Finibus Bonorum et Malorum" (The Extremes of Good and Evil) by Cicero, written in 45 BC. This book is a treatise on the theory of ethics, very popular during the Renaissance. The first line of Lorem Ipsum, "Lorem ipsum dolor sit amet..", comes from a line in section 1.10.32.</p>
      <p>The standard chunk of Lorem Ipsum used since the 1500s is reproduced below for those interested. Sections 1.10.32 and 1.10.33 from "de Finibus Bonorum et Malorum" by Cicero are also reproduced in their exact original form, accompanied by English versions from the 1914 translation by H. Radford.</p>
      <p>There are many variations of passages of Lorem Ipsum available, but the majority have suffered alteration in some form, by injected humour, or randomised words which don't look even slightly believable. If you are going to use a passage of Lorem Ipsum, you need to be sure there isn't anything embarrassing hidden in the middle of text.</p>
    </div>
    <div class="signature" role="img" aria-label="Handwritten signature of Daniel Rowe"></div>
  </article>

  <ul class="contact-list">
    <li><svg viewBox="0 0 8 8" aria-hidden="true"><path d="M0 2 Q4 -1 8 2 L7 3.5 H5.5 V2.5 H2.5 V3.5 H1 Z M1.5 4 H6.5 L7.5 8 H0.5 Z"/></svg>555-201-4410</li>
    <li><svg viewBox="0 0 8 8" aria-hidden="true"><path d="M2 0 H6 V8 H2 Z M3 1 V6 H5 V1 Z"/></svg>555-201-4422</li>
    <li><svg viewBox="0 0 8 8" aria-hidden="true"><path d="M2 0 H6 V3 H8 V8 H0 V3 H2 Z M3 1 V3 H5 V1 Z"/></svg>555-201-4433</li>
    <li><svg viewBox="0 0 8 8" aria-hidden="true"><path d="M0 1.5 H8 V6.5 H0 Z M0.5 2 L4 4.5 L7.5 2 Z" fill-rule="evenodd"/></svg>info@brightholdrealty.example</li>
  </ul>

  <p class="office-address">2400 Harbor Point Rd, Suite 310,<br>Lakeview, FL 33400<br>www.brightholdrealty.example</p>
</section>

</body>
</html>
```